History of Bramwell Fixture Services Inc

This is to be a large poster (48" x 16' Landscape Orientation) printed by a large format printer. The poster through text and photos will represent the history of our company. The file called "Timeline List 20150318" has the events by date order. Maybe this shouldn't be under poster but we didn't see another category that applied.
Reason: We needed to better organize the pictures and content. We cut down the number of pictures and "event" to 105 instead of the 300 some it was before.
Reason: Upon request i have extended the deadline. I apologize for any inconvenience. I'm new to pixel forum. Let me know if you have anymore feed back from me.
Target Market(s)
This will be the center piece of our office for both customers and clients to view.
Industry/Entity Type
Landscape
Look and feel
Each slider illustrates characteristics of the customer's brand and the style your logo design should communicate.

```html
<!DOCTYPE html>
<html lang="en">
<head>
<meta charset="utf-8">
<title>History of Bramwell Fixture Services Inc</title>
<link rel="stylesheet" href="https://fonts.googleapis.com/css2?family=Oswald:wght@700&family=Archivo+Black&display=swap">
<style>
  :root {
    --panel: #b9b9bb;
    --band: #1b1b72;
    --band-edge: #2c2c8c;
    --pin: #555558;
    --stem: #5a5aa8;
    --caption: #111111;
    --red: #ff2a2a;
    --yellow: #f2ec2a;
    --orange: #f7b23a;
    --magenta: #ff2ad4;
    --cyan: #3cc4f0;
    --green: #3cf03c;
    --teal: #22b4a4;
    --blue: #36a6e6;
  }
  * { box-sizing: border-box; margin: 0; padding: 0; }
  html, body { width: 1200px; height: 1064px; overflow: hidden; background: var(--panel); }
  .timeline { width: 1200px; height: 1064px; display: flex; flex-direction: column; }
  .era { height: 266px; display: flex; flex-direction: column; }
  .events { height: 206px; display: grid; grid-template-columns: repeat(12, 100px); }
  .event { position: relative; padding: 10px 8px 0; }
  .thumb { width: 84px; height: 100px; box-shadow: 1px 1px 3px rgba(0,0,0,.35); }
  .thumb--portrait { background: linear-gradient(120deg, #6b4a32 0%, #a87a56 45%, #e8e2dc 60%, #f4f4f6 100%); }
  .thumb--crew { background: linear-gradient(160deg, #8a7c76 0%, #c9bfb8 40%, #6e6460 70%, #b8a8a0 100%); }
  .thumb--event { background: radial-gradient(circle at 55% 45%, #f26a2a 0%, #d83a3a 22%, #3a5ab8 55%, #8aa0c8 100%); }
  .thumb--van { background: linear-gradient(180deg, #9cb6d6 0%, #dfe6ee 45%, #5c5f66 46%, #3a3c42 100%); }
  .thumb--office { background: linear-gradient(200deg, #d9cdb8 0%, #a99c86 50%, #6e6658 100%); }
  .thumb--site { background: linear-gradient(170deg, #2a3450 0%, #4a5a80 45%, #f2d48a 70%, #7a6a4a 100%); }
  .marker { position: absolute; left: 14px; right: 0; top: 120px; bottom: 0; display: flex; }
  .pin { position: relative; flex: 0 0 18px; height: 18px; border-radius: 50%; background: var(--pin); }
  .pin::after { content: ""; position: absolute; left: 7px; top: 18px; width: 3px; height: 68px; background: var(--stem); }
  .caption { margin-left: 5px; margin-top: 3px; font-family: "Archivo Black", sans-serif; font-size: 11px; line-height: 14px; color: var(--caption); white-space: nowrap; }
  .band { height: 60px; background: var(--band); border-top: 3px solid var(--band-edge); display: grid; grid-template-columns: repeat(12, 100px); align-items: center; }
  .year { font-family: "Oswald", sans-serif; font-weight: 700; font-size: 36px; text-align: center; }
  .y-red { color: var(--red); } .y-yellow { color: var(--yellow); } .y-orange { color: var(--orange); }
  .y-magenta { color: var(--magenta); } .y-cyan { color: var(--cyan); } .y-green { color: var(--green); }
  .y-teal { color: var(--teal); } .y-blue { color: var(--blue); }
</style>
</head>
<body>
<main class="timeline">

  <section class="era">
    <div class="events">
      <div class="event"><div class="thumb thumb--portrait" role="img" aria-label="Photo of the founders"></div><div class="marker"><span class="pin"></span><span class="caption">Company<br>Founded</span></div></div>
      <div class="event"><div class="thumb thumb--van" role="img" aria-label="Photo of the first service truck"></div><div class="marker"><span class="pin"></span><span class="caption">First<br>Truck</span></div></div>
      <div class="event"><div class="thumb thumb--crew" role="img" aria-label="Photo of the first employee"></div><div class="marker"><span class="pin"></span><span class="caption">First<br>Hire</span></div></div>
      <div class="event"><div class="thumb thumb--site" role="img" aria-label="Photo of the contract job site"></div><div class="marker"><span class="pin"></span><span class="caption">Ashford<br>Contract</span></div></div>
      <div class="event"><div class="thumb thumb--office" role="img" aria-label="Photo of the new office"></div><div class="marker"><span class="pin"></span><span class="caption">New<br>Office</span></div></div>
      <div class="event"><div class="thumb thumb--event" role="img" aria-label="Wedding photo"></div><div class="marker"><span class="pin"></span><span class="caption">Dan &amp;<br>Carol</span></div></div>
      <div class="event"><div class="thumb thumb--crew" role="img" aria-label="Photo of the crew"></div><div class="marker"><span class="pin"></span><span class="caption">Crew of<br>Ten</span></div></div>
      <div class="event"><div class="thumb thumb--van" role="img" aria-label="Photo of the service fleet"></div><div class="marker"><span class="pin"></span><span class="caption">Fleet<br>Grows</span></div></div>
      <div class="event"><div class="thumb thumb--site" role="img" aria-label="Photo of lamp recycling bins"></div><div class="marker"><span class="pin"></span><span class="caption">Lamp<br>Recycle</span></div></div>
      <div class="event"><div class="thumb thumb--office" role="img" aria-label="Photo of a store interior"></div><div class="marker"><span class="pin"></span><span class="caption">Retail<br>Accounts</span></div></div>
      <div class="event"><div class="thumb thumb--portrait" role="img" aria-label="Photo of the second shop"></div><div class="marker"><span class="pin"></span><span class="caption">Second<br>Shop</span></div></div>
      <div class="event"><div class="thumb thumb--event" role="img" aria-label="Photo of the year end party"></div><div class="marker"><span class="pin"></span><span class="caption">Y2K<br>Ready</span></div></div>
    </div>
    <div class="band">
      <span class="year y-red">1990</span><span class="year y-red">1990</span><span class="year y-red">1991</span><span class="year y-red">1991</span>
      <span class="year y-yellow">1992</span><span class="year y-magenta">1993</span><span class="year y-cyan">1994</span><span class="year y-yellow">1995</span>
      <span class="year y-green">1996</span><span class="year y-red">1997</span><span class="year y-red">1998</span><span class="year y-magenta">1999</span>
    </div>
  </section>

  <section class="era">
    <div class="events">
      <div class="event"><div class="thumb thumb--event" role="img" aria-label="Photo of the new year celebration"></div><div class="marker"><span class="pin"></span><span class="caption">New<br>Century</span></div></div>
      <div class="event"><div class="thumb thumb--van" role="img" aria-label="Photo of the bucket truck"></div><div class="marker"><span class="pin"></span><span class="caption">Bucket<br>Truck</span></div></div>
      <div class="event"><div class="thumb thumb--site" role="img" aria-label="Photo of an illuminated sign"></div><div class="marker"><span class="pin"></span><span class="caption">Sign<br>Division</span></div></div>
      <div class="event"><div class="thumb thumb--office" role="img" aria-label="Photo of the expanded office"></div><div class="marker"><span class="pin"></span><span class="caption">Office<br>Expands</span></div></div>
      <div class="event"><div class="thumb thumb--crew" role="img" aria-label="Photo of the safety team"></div><div class="marker"><span class="pin"></span><span class="caption">Safety<br>Award</span></div></div>
      <div class="event"><div class="thumb thumb--portrait" role="img" aria-label="Photo of the warehouse"></div><div class="marker"><span class="pin"></span><span class="caption">Warehouse<br>Lease</span></div></div>
      <div class="event"><div class="thumb thumb--site" role="img" aria-label="Photo of LED fixtures"></div><div class="marker"><span class="pin"></span><span class="caption">LED<br>Pilot</span></div></div>
      <div class="event"><div class="thumb thumb--van" role="img" aria-label="Photo of park lights"></div><div class="marker"><span class="pin"></span><span class="caption">Park<br>Lighting</span></div></div>
      <div class="event"><div class="thumb thumb--crew" role="img" aria-label="Photo of the staff"></div><div class="marker"><span class="pin"></span><span class="caption">Twenty<br>Staff</span></div></div>
      <div class="event"><div class="thumb thumb--event" role="img" aria-label="Family photo"></div><div class="marker"><span class="pin"></span><span class="caption">Kids Join<br>Family</span></div></div>
      <div class="event"><div class="thumb thumb--office" role="img" aria-label="Photo of the website launch"></div><div class="marker"><span class="pin"></span><span class="caption">Website<br>Launch</span></div></div>
      <div class="event"><div class="thumb thumb--site" role="img" aria-label="Photo of a lit parking lot"></div><div class="marker"><span class="pin"></span><span class="caption">Parking<br>Lots</span></div></div>
    </div>
    <div class="band">
      <span class="year y-cyan">2000</span><span class="year y-cyan">2000</span><span class="year y-orange">2001</span><span class="year y-orange">2001</span>
      <span class="year y-orange">2001</span><span class="year y-orange">2001</span><span class="year y-green">2002</span><span class="year y-green">2002</span>
      <span class="year y-yellow">2003</span><span class="year y-cyan">2004</span><span class="year y-red">2005</span><span class="year y-yellow">2006</span>
    </div>
  </section>

  <section class="era">
    <div class="events">
      <div class="event"><div class="thumb thumb--portrait" role="img" aria-label="Photo of the new manager"></div><div class="marker"><span class="pin"></span><span class="caption">New<br>Manager</span></div></div>
      <div class="event"><div class="thumb thumb--site" role="img" aria-label="Photo of a hospital job"></div><div class="marker"><span class="pin"></span><span class="caption">Hospital<br>Contract</span></div></div>
      <div class="event"><div class="thumb thumb--van" role="img" aria-label="Photo of new trucks"></div><div class="marker"><span class="pin"></span><span class="caption">Five New<br>Trucks</span></div></div>
      <div class="event"><div class="thumb thumb--crew" role="img" aria-label="Photo of the service team"></div><div class="marker"><span class="pin"></span><span class="caption">24 Hour<br>Service</span></div></div>
      <div class="event"><div class="thumb thumb--office" role="img" aria-label="Photo of the training room"></div><div class="marker"><span class="pin"></span><span class="caption">Training<br>Center</span></div></div>
      <div class="event"><div class="thumb thumb--event" role="img" aria-label="Photo of the anniversary party"></div><div class="marker"><span class="pin"></span><span class="caption">20 Year<br>Party</span></div></div>
      <div class="event"><div class="thumb thumb--site" role="img" aria-label="Photo of a solar light install"></div><div class="marker"><span class="pin"></span><span class="caption">Solar<br>Installs</span></div></div>
      <div class="event"><div class="thumb thumb--portrait" role="img" aria-label="Photo of a school job"></div><div class="marker"><span class="pin"></span><span class="caption">School<br>District</span></div></div>
      <div class="event"><div class="thumb thumb--van" role="img" aria-label="Photo of highway lights"></div><div class="marker"><span class="pin"></span><span class="caption">Highway<br>Work</span></div></div>
      <div class="event"><div class="thumb thumb--crew" role="img" aria-label="Photo of the growing team"></div><div class="marker"><span class="pin"></span><span class="caption">Forty<br>Staff</span></div></div>
      <div class="event"><div class="thumb thumb--office" role="img" aria-label="Photo of the dispatch desk"></div><div class="marker"><span class="pin"></span><span class="caption">Dispatch<br>System</span></div></div>
      <div class="event"><div class="thumb thumb--event" role="img" aria-label="Photo of a community event"></div><div class="marker"><span class="pin"></span><span class="caption">Charity<br>Drive</span></div></div>
    </div>
    <div class="band">
      <span class="year y-yellow">2007</span><span class="year y-yellow">2008</span><span class="year y-yellow">2008</span><span class="year y-yellow">2009</span>
      <span class="year y-yellow">2009</span><span class="year y-teal">2010</span><span class="year y-teal">2010</span><span class="year y-teal">2010</span>
      <span class="year y-orange">2011</span><span class="year y-orange">2011</span><span class="year y-orange">2011</span><span class="year y-orange">2011</span>
    </div>
  </section>

  <section class="era">
    <div class="events">
      <div class="event"><div class="thumb thumb--office" role="img" aria-label="Photo of the headquarters"></div><div class="marker"><span class="pin"></span><span class="caption">New<br>HQ</span></div></div>
      <div class="event"><div class="thumb thumb--site" role="img" aria-label="Photo of an LED retrofit"></div><div class="marker"><span class="pin"></span><span class="caption">LED<br>Retrofits</span></div></div>
      <div class="event"><div class="thumb thumb--crew" role="img" aria-label="Photo of the crew"></div><div class="marker"><span class="pin"></span><span class="caption">Crew<br>Award</span></div></div>
      <div class="event"><div class="thumb thumb--van" role="img" aria-label="Photo of the lift truck"></div><div class="marker"><span class="pin"></span><span class="caption">Lift<br>Fleet</span></div></div>
      <div class="event"><div class="thumb thumb--portrait" role="img" aria-label="Photo of the next generation"></div><div class="marker"><span class="pin"></span><span class="caption">Next<br>Leaders</span></div></div>
      <div class="event"><div class="thumb thumb--site" role="img" aria-label="Photo of a stadium job"></div><div class="marker"><span class="pin"></span><span class="caption">Stadium<br>Lights</span></div></div>
      <div class="event"><div class="thumb thumb--event" role="img" aria-label="Photo of the open house"></div><div class="marker"><span class="pin"></span><span class="caption">Open<br>House</span></div></div>
      <div class="event"><div class="thumb thumb--office" role="img" aria-label="Photo of the new branch"></div><div class="marker"><span class="pin"></span><span class="caption">Branch<br>Opens</span></div></div>
      <div class="event"><div class="thumb thumb--crew" role="img" aria-label="Photo of the full staff"></div><div class="marker"><span class="pin"></span><span class="caption">Sixty<br>Staff</span></div></div>
      <div class="event"><div class="thumb thumb--van" role="img" aria-label="Photo of electric vans"></div><div class="marker"><span class="pin"></span><span class="caption">Electric<br>Vans</span></div></div>
      <div class="event"><div class="thumb thumb--event" role="img" aria-label="Photo of the 25th anniversary"></div><div class="marker"><span class="pin"></span><span class="caption">25 Years<br>Strong</span></div></div>
      <div class="event"><div class="thumb thumb--portrait" role="img" aria-label="Photo of the owners today"></div><div class="marker"><span class="pin"></span><span class="caption">Dan &amp;<br>Carol</span></div></div>
    </div>
    <div class="band">
      <span class="year y-blue">2012</span><span class="year y-blue">2012</span><span class="year y-blue">2012</span><span class="year y-blue">2012</span>
      <span class="year y-yellow">2013</span><span class="year y-yellow">2013</span><span class="year y-yellow">2013</span><span class="year y-yellow">2013</span>
      <span class="year y-green">2014</span><span class="year y-green">2014</span><span class="year y-orange">2015</span><span class="year y-orange">2015</span>
    </div>
  </section>

</main>
</body>
</html>
```